Now Leasing Banner

Looking for a banner that says the following information approx 4' x 30'

Now Leasing Maplebrook Terrace 925-318-6042

Target Market(s)

Drive by traffic

Industry/Entity Type

Residential property management

Requirements
Must have
• Clear and readable from a distance

```html
<!DOCTYPE html>
<html lang="en">
<head>
<meta charset="utf-8">
<title>Now Leasing Banner</title>
<link rel="stylesheet" href="https://fonts.googleapis.com/css2?family=Oswald:wght@700&display=swap">
<style>
  :root {
    --panel-dark: #1c1c1c;
    --headline-white: #ffffff;
    --phone-yellow: #e5ff00;
  }
  html, body {
    margin: 0;
    padding: 0;
    overflow: hidden;
    background: var(--panel-dark);
  }
  .banner {
    position: relative;
    width: 1200px;
    height: 160px;
    overflow: hidden;
    background: var(--panel-dark);
    font-family: "Oswald", "Arial Narrow", sans-serif;
    font-weight: 700;
  }
  .aerial-photo {
    position: absolute;
    inset: 0;
    width: 1200px;
    height: 160px;
  }
  .headline,
  .phone-number {
    position: absolute;
    top: 0;
    height: 160px;
    margin: 0;
    line-height: 160px;
    text-align: center;
    text-shadow: 2px 3px 4px rgba(0, 0, 0, 0.6);
    white-space: nowrap;
  }
  .headline {
    left: 20px;
    width: 724px;
    color: var(--headline-white);
    font-size: 52px;
    letter-spacing: 0.3px;
  }
  .phone-number {
    left: 772px;
    width: 412px;
    color: var(--phone-yellow);
    font-size: 66px;
    letter-spacing: 1px;
  }
</style>
</head>
<body>
  <div class="banner">
    <svg class="aerial-photo" viewBox="0 0 1200 160" xmlns="http://www.w3.org/2000/svg">
      <defs>
        <linearGradient id="aerialTone" x1="0" y1="0" x2="1" y2="0.3">
          <stop offset="0" stop-color="#2a2e26"/>
          <stop offset="0.35" stop-color="#33392b"/>
          <stop offset="0.6" stop-color="#3b4a2c"/>
          <stop offset="1" stop-color="#2f3a24"/>
        </linearGradient>
      </defs>
      <rect width="780" height="160" fill="url(#aerialTone)" role="img"
            aria-label="Darkened aerial photo of the apartment community, landscaped hills and a nearby highway"/>
      <path class="dark-panel" d="M764 0 Q752 80 758 160 L1200 160 L1200 0 Z" fill="var(--panel-dark)"/>
    </svg>
    <h1 class="headline">Now Leasing Maplebrook Terrace</h1>
    <p class="phone-number">925-318-6042</p>
  </div>
</body>
</html>
```